MV Personal Name/Business Card.

I need a double-sided name card with a logo/full design incorporating the "themes/concepts" of:
Neurology, wellness, Animals, Healing, Chiropractic, lifestyle, energy, creatvity & color on both sides of the card.
Information to include:
Name: Miranda Voss
Mobile #: 0471 862 913
Email chiromvh@pelomail.com

Possible use of "MV Health & Chiropractic"

Target Market(s)

People of all ages looking to improve their health & lifestyle.

Industry/Entity Type

Business

```html
<!DOCTYPE html>
<html lang="en">
<head>
<meta charset="utf-8">
<title>MV Health &amp; Chiropractic — Business Card</title>
<link rel="stylesheet" href="https://fonts.googleapis.com/css2?family=Open+Sans:wght@400;600;700&display=swap">
<style>
  :root {
    --page-bg: #e9e7e3;
    --card-dark: #2e2e2e;
    --card-arc: #363636;
    --card-light: #f1f1f1;
    --accent-blue: #0895cf;
    --ink-dark: #1f1f1f;
    --ink-light: #f4f4f4;
  }
  * { margin: 0; padding: 0; box-sizing: border-box; }
  html, body {
    width: 1200px;
    height: 676px;
    overflow: hidden;
    background: var(--page-bg);
    font-family: "Open Sans", sans-serif;
  }
  .card-spread {
    position: relative;
    width: 1200px;
    height: 676px;
    display: flex;
    align-items: center;
    justify-content: center;
    gap: 40px;
  }
  .card {
    position: relative;
    width: 540px;
    height: 310px;
    overflow: hidden;
    border-radius: 3px;
    box-shadow: 0 6px 18px rgba(0, 0, 0, 0.18);
  }
  .card-art {
    position: absolute;
    inset: 0;
    width: 100%;
    height: 100%;
  }
  /* Front */
  .identity {
    position: absolute;
    left: 24px;
    top: 20px;
  }
  .identity-name {
    font-size: 20px;
    font-weight: 700;
    color: var(--ink-dark);
    line-height: 1.15;
  }
  .identity-practice {
    font-size: 12.5px;
    color: var(--accent-blue);
    margin-left: 8px;
  }
  .contact-list {
    position: absolute;
    right: 26px;
    top: 168px;
    list-style: none;
    text-align: right;
    font-size: 13.5px;
    line-height: 1.42;
    color: var(--ink-light);
  }
  .contact-item {
    display: flex;
    justify-content: flex-end;
    align-items: center;
    gap: 7px;
  }
  .contact-icon {
    width: 11px;
    height: 11px;
    flex: none;
  }
  .contact-icon-spacer { width: 11px; flex: none; }
  .contact-web { color: var(--accent-blue); letter-spacing: 0.4px; }
  /* Back */
  .card-back { background: var(--card-dark); }
  .theme-lines {
    position: absolute;
    left: 30px;
    top: 160px;
    font-size: 15.5px;
    line-height: 1.45;
    color: var(--ink-light);
    white-space: nowrap;
  }
</style>
</head>
<body>
<main class="card-spread">
  <section class="card card-front" aria-label="Card front">
    <svg class="card-art" viewBox="0 0 540 310" aria-hidden="true">
      <rect width="540" height="310" fill="var(--card-light)"/>
      <path d="M0,160 Q150,75 315,0 L395,0 Q175,95 0,208 Z" fill="var(--accent-blue)"/>
      <path d="M0,208 Q175,95 395,0 L540,0 L540,310 L0,310 Z" fill="var(--card-dark)"/>
    </svg>
    <div class="identity">
      <h1 class="identity-name">Miranda Voss</h1>
      <p class="identity-practice">MV Health &amp; Chiropractic</p>
    </div>
    <ul class="contact-list">
      <li class="contact-item"><span>0471 862 913</span>
        <svg class="contact-icon" viewBox="0 0 12 12" aria-hidden="true"><rect x="3" y="0.5" width="6" height="11" rx="1.2" fill="none" stroke="var(--accent-blue)" stroke-width="1.2"/><rect x="5" y="9.2" width="2" height="1" fill="var(--accent-blue)"/></svg>
      </li>
      <li class="contact-item"><span>chiromvh@pelomail.com</span>
        <svg class="contact-icon" viewBox="0 0 12 12" aria-hidden="true"><rect x="0.5" y="2.5" width="11" height="7" fill="var(--accent-blue)"/><path d="M0.8,2.8 L6,6.6 L11.2,2.8" fill="none" stroke="var(--card-dark)" stroke-width="1"/></svg>
      </li>
      <li class="contact-item contact-web"><span>www.mvhealthchiro.com</span><span class="contact-icon-spacer"></span></li>
    </ul>
  </section>

  <section class="card card-back" aria-label="Card back">
    <svg class="card-art" viewBox="0 0 540 310" aria-hidden="true">
      <path d="M0,120 Q120,40 300,0 L360,0 Q170,55 0,160 Z" fill="var(--card-arc)"/>
    </svg>
    <p class="theme-lines">Neurology | Wellness | Animals | Healing | Chiropractic<br>Lifestyle | Energy | Creatvity &amp; color on both sides.</p>
  </section>
</main>
</body>
</html>
```